8x8 Social Media Ad - Brant Summit Expo

Attention Real Estate Agents
Please join us for our
Quarterly Real Estate Training Expo
The 2nd Saturday of February, May, August and November
Our Next Training Expo is _________________________________
From 9 am to 1 pm
at
Halvorne Suites Millbrook Court
4817 Copper Willow Lane, Dunmere, MD 20588
Scheduled Speakers
9:00 am - Marcus Pellington - Orientation
9:30 am - Derrin Oakfield - Multiple Income Streams / Crest Program
10:00 am - Talia Brennick - Marketing though Social Media
10:45 am - Rex Dunmore - Generating Business through Ru-Plaza
11:30 am - Kemi Adeyoro - Real Estate Investing
12:15 pm - Gregor Tamsey - (Main Speaker) Training Topic TBA
For more information call Marcus Pellington at (240) 555-0183 or email mpellington@brantsummithomes.example

```html
<!DOCTYPE html>
<html lang="en">
<head>
<meta charset="utf-8">
<title>Brant Summit Expo – Quarterly Real Estate Training Expo</title>
<link href="https://fonts.googleapis.com/css2?family=Montserrat:ital,wght@0,400;0,500;0,700;0,800;0,900;1,300;1,400;1,500;1,800;1,900&display=swap" rel="stylesheet">
<style>
:root{
  --teal-deep:#0d6664;
  --teal-panel:#137673;
  --teal-label:#0b5553;
  --teal-bright:#0aa9a7;
  --cyan:#3ee4da;
  --yellow:#f6e61a;
  --ink:#0e5a58;
  --white:#ffffff;
}
*{margin:0;padding:0;box-sizing:border-box}
html,body{width:1200px;height:1200px;overflow:hidden;background:var(--white)}
body{font-family:'Montserrat',sans-serif;color:var(--ink)}
.ad{position:relative;width:1200px;height:1200px;background:var(--white);overflow:hidden}

.teal-band{position:absolute;left:480px;top:322px;width:720px;height:334px;background:var(--teal-bright)}
.speaker-panel{position:absolute;left:0;top:34px;width:494px;height:1046px;background:var(--teal-panel);border-radius:0 86px 0 0}
.footer-bar{position:absolute;left:0;top:1110px;width:1200px;height:90px;background:var(--teal-deep)}

.brand{position:absolute;left:50px;top:82px;display:flex;align-items:center;gap:12px;color:var(--white);font-weight:900;font-size:34px;letter-spacing:1px}
.brand-dot{width:22px;height:22px;border-radius:50%;background:var(--cyan)}

.speakers-label{position:absolute;left:42px;top:198px;width:426px;height:58px;background:var(--teal-label);transform:skewX(-10deg);display:flex;align-items:center;justify-content:center}
.speakers-label span{transform:skewX(10deg);color:var(--white);font-size:25px;font-weight:500;letter-spacing:.5px}
.speakers-label b{color:var(--cyan);font-weight:800}

.speaker{position:absolute;left:36px;width:440px;height:126px}
.speaker-photo{position:absolute;left:0;top:0;width:124px;height:124px;border-radius:50%;background:radial-gradient(circle at 50% 40%,#2a3a40 0 36%,var(--cyan) 37%)}
.speaker-info{position:absolute;left:140px;top:6px;color:var(--white)}
.speaker-time{font-size:26px;font-style:italic;font-weight:400;line-height:1.1}
.speaker-name{margin-top:6px;font-size:21px;font-weight:800;color:var(--cyan);letter-spacing:.3px;text-transform:uppercase}
.speaker-topic{margin-top:4px;font-size:14.5px;font-weight:700;text-transform:uppercase;line-height:1.25}

.headline{position:absolute;left:500px;width:690px;text-align:center;font-style:italic;text-transform:uppercase;line-height:1}
.headline.top{top:98px;font-size:64px;font-weight:400;color:var(--ink)}
.headline.bottom{top:164px;font-size:64px;font-weight:900;color:var(--ink)}

.invite-banner{position:absolute;left:540px;top:262px;width:612px;height:78px;background:var(--yellow);transform:skewX(-14deg);display:flex;align-items:center;justify-content:center}
.invite-banner span{transform:skewX(14deg);font-size:37px;font-weight:500;color:var(--ink)}
.invite-banner b{font-style:italic;font-weight:900}

.expo-title{position:absolute;left:500px;top:366px;width:690px;text-align:center;font-style:italic;text-transform:uppercase;line-height:64px;font-size:68px;color:var(--white)}
.expo-title .light{font-weight:300}
.expo-title .heavy{font-weight:900}
.expo-title .hl{color:var(--yellow);font-weight:900}

.schedule{position:absolute;left:500px;top:702px;width:690px;text-align:center;text-transform:uppercase;color:var(--ink);font-size:40px;line-height:44px}
.schedule .strong{font-weight:900}
.schedule .soft{font-weight:500}

.venue{position:absolute;left:566px;top:950px;display:flex;gap:22px;align-items:flex-start}
.venue svg{flex:none;margin-top:8px}
.venue p{font-size:25px;font-weight:500;line-height:33px;text-transform:uppercase;color:var(--ink)}

.footer-call{position:absolute;left:26px;top:1136px;color:var(--white);font-size:16.5px;font-weight:500;line-height:18px;text-transform:uppercase}
.footer-phone{position:absolute;left:304px;top:1136px;display:flex;align-items:center;gap:8px;color:var(--white);font-size:36px;font-weight:800}
.footer-email{position:absolute;left:660px;top:1122px;width:530px;text-align:center;color:var(--white);text-transform:uppercase;font-weight:500}
.footer-email .lead{font-size:24px;line-height:28px}
.footer-email .addr{font-size:19.5px;line-height:32px}
</style>
</head>
<body>
<main class="ad">
  <div class="teal-band"></div>
  <section class="speaker-panel"></section>
  <div class="footer-bar"></div>

  <div class="brand"><span class="brand-dot"></span>BRANT SUMMIT</div>

  <div class="speakers-label"><span>SCHEDULED <b>SPEAKERS</b></span></div>

  <div class="speaker" style="top:274px">
    <div class="speaker-photo" role="img" aria-label="Portrait photo of Marcus Pellington"></div>
    <div class="speaker-info"><div class="speaker-time">9:00 AM</div><div class="speaker-name">Marcus Pellington</div><div class="speaker-topic">Orientation</div></div>
  </div>
  <div class="speaker" style="top:400px">
    <div class="speaker-photo" role="img" aria-label="Portrait photo of Derrin Oakfield"></div>
    <div class="speaker-info"><div class="speaker-time">9:30 AM</div><div class="speaker-name">Derrin Oakfield</div><div class="speaker-topic">Multiple Income<br>Streams / Crest Program</div></div>
  </div>
  <div class="speaker" style="top:526px">
    <div class="speaker-photo" role="img" aria-label="Portrait photo of Talia Brennick"></div>
    <div class="speaker-info"><div class="speaker-time" style="font-style:normal">10:00 AM</div><div class="speaker-name">Talia Brennick</div><div class="speaker-topic">Marketing<br>though Social Media</div></div>
  </div>
  <div class="speaker" style="top:658px">
    <div class="speaker-photo" role="img" aria-label="Portrait photo of Rex Dunmore"></div>
    <div class="speaker-info"><div class="speaker-time">10:45 AM</div><div class="speaker-name">Rex Dunmore</div><div class="speaker-topic">Generating Business<br>through Ru-Plaza</div></div>
  </div>
  <div class="speaker" style="top:790px">
    <div class="speaker-photo" role="img" aria-label="Portrait photo of Kemi Adeyoro"></div>
    <div class="speaker-info"><div class="speaker-time">11:30 AM</div><div class="speaker-name">Kemi Adeyoro</div><div class="speaker-topic">Real Estate Investing</div></div>
  </div>
  <div class="speaker" style="top:922px">
    <div class="speaker-photo" role="img" aria-label="Portrait photo of Gregor Tamsey"></div>
    <div class="speaker-info"><div class="speaker-time">12:15 PM</div><div class="speaker-name">Gregor Tamsey</div><div class="speaker-topic">(Main Speaker)<br>Training Topic TBA</div></div>
  </div>

  <h1 class="headline top">Attention Real</h1>
  <h1 class="headline bottom">Estate Agents</h1>

  <div class="invite-banner"><span>PLEASE JOIN <b>US FOR OUR</b></span></div>

  <h2 class="expo-title">
    <span class="light">Quarterly</span><br>
    <span class="light">Real </span><span class="heavy">Estate</span><br>
    <span class="hl">Training</span><br>
    <span class="hl">Expo</span>
  </h2>

  <div class="schedule">
    <div class="strong">The 2nd Saturday of<br>February, May, August<br>and November</div>
    <div class="soft">Our next training expo</div>
    <div class="strong">is from 9 am to 1 pm</div>
  </div>

  <div class="venue">
    <svg width="34" height="46" viewBox="0 0 34 46" aria-hidden="true"><path d="M17 0C7.6 0 0 7.6 0 17c0 12.5 17 29 17 29s17-16.5 17-29C34 7.6 26.4 0 17 0z" fill="var(--ink)"/><circle cx="17" cy="17" r="6.5" fill="var(--white)"/></svg>
    <p>At Halvorne Suites Millbrook<br>Court 4817 Copper Willow<br>Lane, Dunmere,<br>MD 20588.</p>
  </div>

  <div class="footer-call">For more information<br>call Marcus Pellington at</div>
  <div class="footer-phone">
    <svg width="32" height="32" viewBox="0 0 32 32" aria-hidden="true"><circle cx="16" cy="16" r="16" fill="var(--white)"/><path d="M11.5 8.5l2.8 0 1.3 4-1.9 1.5c.9 2 2.4 3.5 4.3 4.4l1.5-1.9 4 1.3v2.8c0 .9-.8 1.6-1.7 1.5C15.6 21.6 10.4 16.4 10 10.2c-.1-.9.6-1.7 1.5-1.7z" fill="var(--teal-deep)"/></svg>
    (240) 555-0183
  </div>
  <div class="footer-email"><div class="lead">Or email</div><div class="addr">mpellington@brantsummithomes.example</div></div>
</main>
</body>
</html>
```